Velmarotix - world unique technology for better life - please let them know who am i at first sight

We need a new business card for company which is a provider of unique crystal based technology suitable for all living being. For more information and final design you can use our brochure (our colours are black and blue from brochure).
We use Verdana font

Industry/Entity Type

Business

Contact Information for Business Card

regular dimension

Font styles to use
Other font styles liked:
• Verdana

Requirements
Must have
• Logo
• name
• function/position
• phone
• mobile
• e-mail
• adress
Nice to have
• inovative design (technology directed)

```html
<!DOCTYPE html>
<html lang="en">
<head>
<meta charset="utf-8">
<title>Velmarotix – Business Card</title>
<link rel="stylesheet" href="https://fonts.googleapis.com/css2?family=Open+Sans:wght@400;700&display=swap">
<style>
  :root {
    --page-bg: #e9eaec;
    --card-black: #060606;
    --brand-blue: #1ea6e4;
    --text-white: #f2f2f2;
    --text-muted: #cfcfcf;
    --divider: #6b6b6b;
  }
  * { box-sizing: border-box; margin: 0; padding: 0; }
  html, body {
    width: 1200px; height: 948px; overflow: hidden;
    background: var(--page-bg);
    font-family: "Open Sans", Verdana, sans-serif;
  }
  .sheet {
    position: relative; width: 1200px; height: 948px;
  }
  .card {
    position: absolute; left: 250px; width: 700px; height: 400px;
    background: var(--card-black);
    box-shadow: 0 10px 30px rgba(0,0,0,.25);
    overflow: hidden;
  }
  .card--front { top: 54px; }
  .card--back  { top: 494px; }

  .brand {
    position: absolute; display: flex; align-items: center; gap: 18px;
  }
  .brand__dot {
    width: 62px; height: 62px; border-radius: 50%;
    background: var(--brand-blue);
  }
  .brand__name {
    color: var(--brand-blue); font-weight: 400;
    font-size: 46px; letter-spacing: 2px; line-height: 1;
  }
  .card--front .brand { left: 238px; top: 52px; }

  .person {
    position: absolute; left: 52px; top: 170px; width: 250px;
  }
  .person__name {
    color: var(--brand-blue); font-weight: 700; font-size: 22px; margin-bottom: 6px;
  }
  .person__role, .person__address {
    color: var(--text-white); font-size: 15px; line-height: 1.55;
  }
  .contact-divider {
    position: absolute; left: 322px; top: 172px; width: 1px; height: 118px;
    background: var(--divider);
  }
  .contacts {
    position: absolute; left: 344px; top: 176px; list-style: none;
  }
  .contacts__item {
    display: flex; align-items: center; gap: 12px;
    color: var(--text-white); font-size: 15px; height: 36px;
  }
  .contacts__icon { width: 18px; height: 18px; fill: var(--text-muted); }

  .card__rule {
    position: absolute; left: 0; right: 0; bottom: 80px; height: 2px;
    background: var(--text-white);
  }
  .web-band {
    position: absolute; left: 0; right: 0; bottom: 0; height: 74px;
    background: var(--brand-blue);
    display: flex; align-items: center; justify-content: center;
    color: var(--text-white); font-size: 26px; letter-spacing: 3px;
  }

  .card--back .brand { left: 50%; top: 130px; transform: translateX(-50%); }
  .card--back .brand__dot { width: 78px; height: 78px; }
  .card--back .brand__name { font-size: 54px; }
  .back-web {
    position: absolute; left: 0; right: 0; top: 250px; text-align: center;
    color: var(--text-white); font-weight: 700; font-size: 22px; letter-spacing: 4px;
  }
</style>
</head>
<body>
<main class="sheet">

  <section class="card card--front" aria-label="Business card front">
    <div class="brand">
      <span class="brand__dot"></span>
      <span class="brand__name">VELMAROTIX</span>
    </div>

    <div class="person">
      <p class="person__name">Mirela Kovanic</p>
      <p class="person__role">Founder and CEO</p>
      <p class="person__address">Street Name, CityName<br>Zipcode-0124</p>
    </div>

    <div class="contact-divider"></div>

    <ul class="contacts">
      <li class="contacts__item">
        <svg class="contacts__icon" viewBox="0 0 24 24" aria-hidden="true"><path d="M6.6 10.8a15 15 0 0 0 6.6 6.6l2.2-2.2a1 1 0 0 1 1-.25 11.4 11.4 0 0 0 3.6.6 1 1 0 0 1 1 1V20a1 1 0 0 1-1 1A17 17 0 0 1 3 4a1 1 0 0 1 1-1h3.5a1 1 0 0 1 1 1c0 1.25.2 2.45.6 3.6a1 1 0 0 1-.25 1z"/></svg>
        012-555-0147
      </li>
      <li class="contacts__item">
        <svg class="contacts__icon" viewBox="0 0 24 24" aria-hidden="true"><path d="M7 1h10a2 2 0 0 1 2 2v18a2 2 0 0 1-2 2H7a2 2 0 0 1-2-2V3a2 2 0 0 1 2-2zm0 3v14h10V4zm5 15.5a1 1 0 1 0 0 2 1 1 0 0 0 0-2z"/></svg>
        012-555-0147
      </li>
      <li class="contacts__item">
        <svg class="contacts__icon" viewBox="0 0 24 24" aria-hidden="true"><path d="M2 5h20v14H2zm2 2v.5l8 5 8-5V7zm0 2.8V17h16V9.8l-8 5z"/></svg>
        info@velmarotix.cu
      </li>
    </ul>

    <div class="card__rule"></div>
    <div class="web-band">www.velmarotix.cu</div>
  </section>

  <section class="card card--back" aria-label="Business card back">
    <div class="brand">
      <span class="brand__dot"></span>
      <span class="brand__name">VELMAROTIX</span>
    </div>
    <p class="back-web">www.velmarotix.cu</p>
  </section>

</main>
</body>
</html>
```